Modern Business Card

Modern professional business card with more than just logo and demographic info. Something memorable.

We are a trendy/modern chiropractic group with an emphasis on neurology, hence the minimalist-type brain logo. We want to convey that modern and technical aspect with professionalism and the elite nature of our practice environment.

```html
<!DOCTYPE html>
<html lang="en">
<head>
<meta charset="utf-8">
<title>Northvale Spine Clinic – Business Card</title>
<link href="https://fonts.googleapis.com/css2?family=Montserrat:wght@600;700&family=Roboto:wght@400&display=swap" rel="stylesheet">
<style>
  :root {
    --brand-blue: #4680c2;
    --brand-blue-light: #5a93cf;
    --brand-tint: rgba(255,255,255,.08);
    --card-white: #ffffff;
    --ink: #3f3f3f;
    --backdrop: #2b2b2b;
  }
  * { margin: 0; padding: 0; box-sizing: border-box; }
  html, body { width: 1200px; height: 900px; overflow: hidden; }
  body {
    background: var(--backdrop);
    font-family: "Roboto", Arial, sans-serif;
    position: relative;
  }
  .card {
    position: absolute;
    left: 250px;
    width: 700px;
    height: 400px;
    box-shadow: 0 10px 30px rgba(0,0,0,.5);
    overflow: hidden;
  }
  .card--front {
    top: 40px;
    background: linear-gradient(120deg, var(--brand-blue) 40%, var(--brand-blue-light) 100%);
    display: flex;
    align-items: center;
    justify-content: center;
  }
  .card--back {
    top: 465px;
    background: var(--card-white);
  }
  .pattern-area { position: absolute; }
  .card--front .pattern-area {
    left: 190px; top: 40px;
    width: 340px; height: 340px;
    background: var(--brand-tint);
  }
  .card--back .pattern-area {
    left: 440px; top: 185px;
    width: 240px; height: 215px;
    background: var(--brand-blue);
  }
  .brand {
    position: relative;
    display: flex;
    align-items: center;
    gap: 16px;
    font-family: "Montserrat", Arial, sans-serif;
    font-weight: 600;
    text-transform: uppercase;
    letter-spacing: .06em;
  }
  .brand__dot { border-radius: 50%; flex: none; }
  .card--front .brand { color: var(--card-white); font-size: 38px; }
  .card--front .brand__dot { width: 30px; height: 30px; background: var(--card-white); }
  .card--back .brand {
    position: absolute;
    left: 50px; top: 48px;
    color: var(--brand-blue);
    font-size: 24px;
    gap: 10px;
  }
  .card--back .brand__dot { width: 20px; height: 20px; background: var(--brand-blue); }
  .details { position: absolute; left: 50px; top: 130px; }
  .person__name {
    font-family: "Montserrat", Arial, sans-serif;
    font-weight: 700;
    font-size: 26px;
    color: var(--brand-blue);
    text-transform: uppercase;
    letter-spacing: .02em;
  }
  .person__role { font-size: 15px; color: var(--ink); margin-top: 2px; }
  .divider { width: 22px; height: 2px; background: var(--brand-blue); margin: 8px 0; }
  .address { font-size: 15px; color: var(--ink); line-height: 1.4; font-style: normal; }
  .contact-list { list-style: none; font-size: 15px; color: var(--ink); line-height: 1.55; }
  .contact-list li { display: flex; align-items: center; gap: 8px; }
  .contact-list svg { width: 13px; height: 13px; fill: var(--brand-blue); flex: none; }
</style>
</head>
<body>

<section class="card card--front" aria-label="Card front">
  <div class="pattern-area" role="img" aria-label="Faint brand pattern in lighter blue"></div>
  <div class="brand"><span class="brand__dot"></span>Northvale Spine Clinic</div>
</section>

<section class="card card--back" aria-label="Card back">
  <div class="pattern-area" role="img" aria-label="Large brand pattern in blue"></div>
  <div class="brand"><span class="brand__dot"></span>Northvale Spine Clinic</div>

  <div class="details">
    <p class="person__name">Daniel Marsh</p>
    <p class="person__role">Senior Partner</p>
    <div class="divider"></div>
    <address class="address">12 Orchard Lane<br>Westbrook, Cape Town, 7441</address>
    <div class="divider"></div>
    <ul class="contact-list">
      <li><svg viewBox="0 0 16 16"><path d="M3.5 1.5l2.5 3-1.5 1.8c.9 1.9 2.3 3.3 4.2 4.2L10.5 9l3 2.5-1.2 2.8C6.6 14.3 1.7 9.4 1.7 3.7z"/></svg>+120 5550 1834</li>
      <li><svg viewBox="0 0 16 16"><path d="M4.5 1h7v14h-7zM6 2.5v9.5h4V2.5zM7.2 13h1.6v1H7.2z" fill-rule="evenodd"/></svg>+965 5550 2719</li>
      <li><svg viewBox="0 0 16 16"><path d="M1 3.5h14v9H1zM2 4.5l6 4.5 6-4.5z"/></svg>info@northvalespine.com</li>
      <li><svg viewBox="0 0 16 16"><circle cx="8" cy="8" r="6.5" fill="none" stroke-width="1.5" style="stroke:var(--brand-blue)"/><path d="M1.5 7.3h13v1.4h-13zM7.3 1.5h1.4v13H7.3z"/></svg>www.northvalespine.com</li>
    </ul>
  </div>
</section>

</body>
</html>
```